Bright Nook Home Page (A Home Wellness e-commerce site & blog)

We need a dynamic home page created for a home wellness brand. Must be visually appealing and extremely mobile-friendly. Logos and a Navmap have been provided but that is just a guideline, PLEASE USE YOUR CREATIVITY.

Target Market(s)

1st target demo: females 24-48, 2nd target demo: all 24-48

Number of Pages Required

1 page

```html
<!DOCTYPE html>
<html lang="en">
<head>
<meta charset="utf-8">
<title>Bright Nook — Home Wellness</title>
<link href="https://fonts.googleapis.com/css2?family=Archivo:wght@400;600;800&family=Roboto:wght@400;500;700&display=swap" rel="stylesheet">
<style>
:root{
  --purple:#55308f;
  --purple-dark:#3f1f78;
  --teal:#2fbfca;
  --teal-dark:#1ea9b5;
  --ink:#141414;
  --body:#6b6b6b;
  --footer:#1b1b1d;
  --footer-text:#c9c9c9;
  --white:#ffffff;
}
*{box-sizing:border-box;margin:0;padding:0}
html,body{width:1200px;height:3254px;overflow:hidden}
body{position:relative;font-family:'Roboto',sans-serif;color:var(--ink);background:var(--white)}
.abs{position:absolute}
.topbar{left:0;top:0;width:1200px;height:33px;background:var(--purple);color:var(--white);font-size:13px;font-weight:500;display:flex;align-items:center;justify-content:center;gap:7px}
.header{left:0;top:33px;width:1200px;height:83px;background:var(--white);box-shadow:0 1px 0 #eee}
.brand{font-family:'Roboto',sans-serif;font-weight:500;color:var(--purple);letter-spacing:-.5px;display:flex;align-items:center;gap:8px;white-space:nowrap}
.brand .dot{width:12px;height:12px;border-radius:50%;background:var(--teal)}
.header .brand{left:86px;top:22px;font-size:31px}
.nav{left:351px;top:31px;display:flex;gap:22px;font-size:15px;font-weight:500}
.nav a{color:var(--ink);text-decoration:none;position:relative}
.nav a.active{color:var(--teal)}
.nav a.active::after{content:"";position:absolute;left:-2px;right:-2px;top:18px;height:9px;border-bottom:3px solid var(--teal);border-radius:0 0 50% 50%}
.social-top{left:960px;top:32px;display:flex;gap:16px}
.social-top span{width:17px;height:17px;border:1.5px solid var(--ink);border-radius:50%;display:flex;align-items:center;justify-content:center}
.social-top span::after{content:"";width:5px;height:5px;border-radius:50%;background:var(--ink)}
.cart{left:1080px;top:24px;width:32px;height:32px;border-radius:50%;background:var(--teal);display:flex;align-items:center;justify-content:center}
.cart .count{position:absolute;right:-5px;top:-5px;width:14px;height:14px;border-radius:50%;background:var(--purple);color:#fff;font-size:9px;display:flex;align-items:center;justify-content:center}
.hero{left:0;top:116px;width:1200px;height:586px;overflow:hidden;
  background:
    radial-gradient(ellipse 260px 220px at 870px 150px,rgba(255,226,160,.95),rgba(255,200,110,0) 70%),
    radial-gradient(ellipse 240px 320px at 890px 330px,rgba(120,110,150,.55),rgba(120,110,150,0) 70%),
    linear-gradient(175deg,rgba(0,0,0,0) 62%,#6e6a63 63%,#8a857c 80%,#5e5a54 100%),
    linear-gradient(180deg,#e9b067 0%,#f0a24a 22%,#c9782f 40%,#8a5626 55%,#5a4420 70%,#3d3518 100%)}
.hero::before{content:"";position:absolute;inset:0;background:linear-gradient(90deg,rgba(40,20,0,.35),rgba(0,0,0,0) 50%)}
.hero-copy{left:112px;top:174px;color:#fff}
.hero-copy .brand{font-size:56px;font-weight:500}
.hero-copy p{margin-top:20px;font-size:17px;line-height:26px;font-weight:500}
.btn{display:inline-flex;align-items:center;justify-content:center;gap:8px;border-radius:30px;color:#fff;font-weight:700;text-transform:uppercase;font-family:'Roboto',sans-serif;text-decoration:none}
.hero .btn{left:112px;top:342px;width:192px;height:50px;background:linear-gradient(90deg,var(--teal-dark),var(--teal));font-size:16px;box-shadow:0 3px 10px rgba(0,0,0,.2)}
.dots{left:578px;top:533px;display:flex;gap:4px}
.dots span{width:12px;height:12px;border:2px solid #fff;border-radius:50%}
.promo{left:0;top:702px;width:1200px;height:87px;background:var(--purple);color:#fff;font-family:'Archivo',sans-serif;font-weight:600;font-size:23px;display:flex;align-items:center;justify-content:center}
.bliss{left:0;top:868px;width:1200px;text-align:center;font-family:'Archivo',sans-serif;line-height:38px}
.bliss strong{display:block;font-weight:800;font-size:33px}
.bliss span{font-size:30px}
.tile{position:absolute}
.about{left:0;top:1753px;width:1200px;height:431px;background:linear-gradient(90deg,#e6e1dc 0%,#eee9e6 45%,#f1edec 100%)}
.about-art{left:0;top:0;width:600px;height:431px;
  background:
    radial-gradient(ellipse 70px 90px at 390px 140px,rgba(90,150,60,.75),rgba(90,150,60,0) 75%),
    radial-gradient(ellipse 70px 80px at 500px 230px,rgba(80,140,50,.7),rgba(80,140,50,0) 75%),
    radial-gradient(circle 110px at 280px 370px,rgba(150,210,120,.85),rgba(140,90,50,.6) 70%,rgba(0,0,0,0) 72%),
    radial-gradient(ellipse 40px 110px at 360px 230px,rgba(90,45,20,.85),rgba(90,45,20,0) 80%),
    radial-gradient(ellipse 40px 110px at 470px 350px,rgba(80,40,20,.85),rgba(80,40,20,0) 80%),
    radial-gradient(circle 55px at 270px 190px,#fbfbfb,rgba(220,220,220,.5) 80%,rgba(0,0,0,0) 82%),
    radial-gradient(ellipse 110px 90px at 90px 300px,rgba(245,230,190,.95),rgba(245,230,190,0) 80%),
    radial-gradient(ellipse 170px 80px at 110px 40px,rgba(255,255,255,.95),rgba(255,255,255,0) 80%)}
.about h2{left:643px;top:70px;font-family:'Archivo',sans-serif;font-weight:800;font-size:36px}
.about p{left:643px;top:136px;width:428px;font-size:14.5px;line-height:24px;color:var(--body)}
.about .btn{left:643px;top:308px;width:179px;height:45px;background:var(--purple-dark);font-size:15px}
.paylater{left:0;top:2184px;width:1200px;height:117px;background:var(--teal)}
.paylater .partner{left:256px;top:33px;font-size:44px;font-weight:500;color:#1f2a44;display:flex;align-items:center;gap:12px}
.paylater .partner .circ{width:44px;height:44px;border-radius:50%;background:#4a3fd6}
.paylater .divide{left:472px;top:18px;width:1px;height:80px;background:rgba(255,255,255,.5)}
.paylater .line{left:506px;top:40px;font-family:'Archivo',sans-serif;font-weight:800;font-size:28px;color:#fff}
.blog-head{left:0;top:2370px;width:1200px;text-align:center}
.blog-head h2{font-family:'Archivo',sans-serif;font-size:36px;font-weight:800}
.blog-head h2 span{font-weight:400}
.blog-head p{margin-top:8px;font-size:14.5px;color:var(--body)}
.card{position:absolute;top:2478px;width:308px;height:389px;background:#fff;border-radius:10px;box-shadow:0 2px 14px rgba(0,0,0,.12);text-align:center}
.card .thumb{position:absolute;left:7px;top:7px;width:294px;height:202px}
.card .date{position:absolute;left:0;right:0;top:236px;font-size:13.5px;color:var(--teal);display:flex;gap:6px;justify-content:center;align-items:center}
.card h3{position:absolute;left:0;right:0;top:258px;font-size:17px;font-weight:500}
.card p{position:absolute;left:20px;right:20px;top:293px;font-size:14px;line-height:23px;color:var(--body)}
.card .more{position:absolute;left:0;right:0;top:354px;font-size:14.5px;font-weight:700;color:var(--teal);display:flex;gap:6px;justify-content:center;align-items:center}
.arrow{top:2655px}
.footer{left:0;top:2955px;width:1200px;height:299px;background:var(--footer);color:var(--footer-text)}
.footer .brand{left:109px;top:86px;font-size:33px;color:#fff;font-weight:400}
.footer .socials{left:147px;top:140px;display:flex;gap:5px}
.footer .socials span{width:27px;height:27px;border:1px solid #ddd;border-radius:50%;display:flex;align-items:center;justify-content:center}
.footer .socials span::after{content:"";width:7px;height:7px;border-radius:50%;background:#ddd}
.fcol h4{font-size:13.5px;color:#fff;font-weight:700;margin-bottom:18px}
.fcol li{list-style:none;font-size:12px;height:26.5px}
.fcol.company{left:380px;top:48px}
.fcol.info{left:535px;top:48px}
.fcol.news{left:702px;top:48px;width:400px}
.fcol.news p{font-size:12px;line-height:18px}
.email{left:702px;top:137px;width:267px;height:44px;border-radius:22px;background:#fff;color:#666;font-size:12.5px;padding-left:20px;display:flex;align-items:center}
.subscribe{left:976px;top:137px;width:111px;height:44px;border-radius:22px;background:var(--teal);color:#fff;font-weight:700;font-size:15px;display:flex;align-items:center;justify-content:center}
.footer .rule{left:111px;top:240px;width:976px;height:1px;background:#333}
.footer .copy{left:0;width:1200px;top:264px;text-align:center;font-size:11px}
.chat{left:1109px;top:250px;width:40px;height:40px;border-radius:50%;background:var(--teal);display:flex;align-items:center;justify-content:center}
</style>
</head>
<body>

<div class="abs topbar">
  <svg width="14" height="11" viewBox="0 0 14 11"><rect x="0" y="1" width="9" height="6" fill="#fff"/><path d="M9 3h3l2 2v2H9z" fill="#fff"/><circle cx="3" cy="9" r="1.6" fill="#fff"/><circle cx="11" cy="9" r="1.6" fill="#fff"/></svg>
  Free shipping on all orders $50 and over!
</div>

<header class="abs header">
  <div class="abs brand"><span class="dot"></span>BrightNook</div>
  <nav class="abs nav">
    <a class="active" href="#">Shop</a><a href="#">Our Story</a><a href="#">Blog</a><a href="#">Stress Symptoms</a><a href="#">Wellness Practices</a><a href="#">Club Rewards</a>
  </nav>
  <div class="abs social-top"><span></span><span></span><span></span></div>
  <div class="abs cart">
    <svg width="16" height="14" viewBox="0 0 16 14"><path d="M1 1h2l2 8h8l2-6H4" fill="none" stroke="#fff" stroke-width="2"/><circle cx="6" cy="12" r="1.3" fill="#fff"/><circle cx="12" cy="12" r="1.3" fill="#fff"/></svg>
    <span class="count">0</span>
  </div>
</header>

<section class="abs hero" role="img" aria-label="Woman with open arms sitting on a stone wall at sunset over rolling hills">
  <div class="abs hero-copy">
    <div class="brand"><span class="dot" style="width:16px;height:16px"></span>BrightNook</div>
    <p>Lorem ipsum dolor sit amet, consectetur adipiscing elit,<br>sed do eiusmod tempor incididunt ut</p>
  </div>
  <a class="abs btn">Shop Now
    <svg width="15" height="15"><circle cx="7.5" cy="7.5" r="7" fill="#fff"/><path d="M6 4l3.5 3.5L6 11" stroke="#2fbfca" stroke-width="2" fill="none"/></svg></a>
  <div class="abs dots"><span></span><span></span><span></span></div>
</section>

<div class="abs promo">50% off sale going on now! Because saving money also makes us happy</div>

<div class="abs bliss"><strong>The key to total bliss is nurturing the</strong><span>mind, body, and soul</span></div>

<div class="tile" style="left:121px;top:983px;width:306px;height:198px;background:radial-gradient(circle 60px at 70px 150px,rgba(255,230,170,.9),rgba(255,230,170,0)),radial-gradient(ellipse 70px 45px at 150px 90px,#7a4a22,rgba(122,74,34,0) 90%),linear-gradient(160deg,#f6b35a 0%,#e08a2f 45%,#b3541b 100%)" role="img" aria-label="Sauna bucket, towels and candles"></div>
<div class="tile" style="left:447px;top:983px;width:305px;height:198px;background:radial-gradient(ellipse 45px 40px at 200px 120px,#3a3835,rgba(58,56,53,0) 90%),radial-gradient(ellipse 40px 30px at 90px 140px,#555,rgba(85,85,85,0) 90%),radial-gradient(circle 25px at 90px 120px,#fff3d0,rgba(255,243,208,0)),linear-gradient(180deg,#e9e2d8 0%,#d6c8b6 60%,#9a8670 100%)" role="img" aria-label="Candle, stones, soap and oil bottles"></div>
<div class="tile" style="left:773px;top:983px;width:306px;height:634px;background:radial-gradient(ellipse 110px 150px at 150px 330px,#f2eee9,rgba(242,238,233,0) 90%),radial-gradient(ellipse 150px 120px at 160px 520px,#d9a98a,rgba(217,169,138,0) 90%),linear-gradient(180deg,#f3f1ee 0%,#ece7e2 40%,#dcc2ae 75%,#f4f1ee 100%)" role="img" aria-label="Facial mask treatment at a spa"></div>
<div class="tile" style="left:121px;top:1201px;width:306px;height:197px;background:radial-gradient(ellipse 60px 50px at 150px 110px,#f4f1ec,rgba(244,241,236,0) 90%),radial-gradient(ellipse 40px 60px at 50px 140px,#e6e2dc,rgba(230,226,220,0) 90%),linear-gradient(180deg,#3f3f3f 0%,#6d6b67 45%,#d5d0c8 100%)" role="img" aria-label="Rolled towels, stones and candles"></div>
<div class="tile" style="left:447px;top:1201px;width:305px;height:197px;background:radial-gradient(ellipse 30px 60px at 180px 140px,#5a2c12,rgba(90,44,18,0) 90%),radial-gradient(ellipse 60px 35px at 70px 160px,#efe8df,rgba(239,232,223,0) 90%),linear-gradient(180deg,#c9b8a6 0%,#b59f88 55%,#caa984 100%)" role="img" aria-label="Shelf with amber bottles and towels"></div>
<div class="tile" style="left:121px;top:1420px;width:306px;height:197px;background:radial-gradient(circle 55px at 180px 100px,#f5e4b4,rgba(245,228,180,0) 90%),radial-gradient(ellipse 120px 60px at 150px 170px,#8c5a2c,rgba(140,90,44,0) 90%),linear-gradient(150deg,#6b5430 0%,#b99460 50%,#ead6a6 100%)" role="img" aria-label="Shea butter jar and nuts on a tray"></div>
<div class="tile" style="left:447px;top:1420px;width:305px;height:197px;background:radial-gradient(ellipse 35px 70px at 220px 120px,#3d1e0c,rgba(61,30,12,0) 90%),radial-gradient(ellipse 45px 55px at 80px 110px,#f8f6f2,rgba(248,246,242,0) 90%),linear-gradient(90deg,#ecebe8 0%,#e2ddd6 60%,#7a4a2a 100%)" role="img" aria-label="Cotton swabs and amber dropper bottles"></div>

<section class="abs about">
  <div class="abs about-art" role="img" aria-label="Flat lay of towels, cream jar, soap, bath salts, leaves and amber bottles"></div>
  <h2 class="abs">About <span style="font-weight:400">Us</span></h2>
  <p class="abs">They say that home is where the heart is. But home is also where your mind and body reside. At Bright Nook we believe that home should be your place of Zen. A respite from the crazy world outside those walls. It is where you recharge your soul so you can approach each day with the focus and energy necessary to conquer the world.</p>
  <a class="abs btn">Tell Me More
    <svg width="14" height="14"><circle cx="7" cy="7" r="6.5" fill="#fff"/><path d="M5.5 4l3 3-3 3" stroke="#3f1f78" stroke-width="2" fill="none"/></svg></a>
</section>

<section class="abs paylater">
  <div class="abs partner"><span class="circ"></span>Tallypay</div>
  <div class="abs divide"></div>
  <div class="abs line">Don’t sweat it. You can pay later.</div>
</section>

<div class="abs blog-head"><h2>Bright <span>Blog</span></h2><p>Food for the mind, tips for the body and exercises for the soul</p></div>

<svg class="abs arrow" style="left:42px" width="24" height="40"><path d="M20 2L4 20l16 18" stroke="#999" stroke-width="3" fill="none"/></svg>
<svg class="abs arrow" style="left:1131px" width="24" height="40"><path d="M4 2l16 18L4 38" stroke="#999" stroke-width="3" fill="none"/></svg>

<article class="card" style="left:111px">
  <div class="thumb" role="img" aria-label="Bath with rose petals and bottles on a tray" style="background:radial-gradient(ellipse 90px 30px at 190px 70px,#7a3a22,rgba(122,58,34,0) 90%),linear-gradient(180deg,#3f5a50 0%,#8fa69a 35%,#f0eded 48%,#e85a6a 62%,#c92a3e 100%)"></div>
  <div class="date"><svg width="12" height="12"><rect x="1" y="2" width="10" height="9" fill="none" stroke="#2fbfca" stroke-width="1.5"/><path d="M1 5h10" stroke="#2fbfca" stroke-width="1.2"/></svg>April 27, 2021</div>
  <h3>Lorem ipsum dolor sit amet</h3>
  <p>Sed ut perspiciatis unde omnis iste natus error sit voluptatem accusantium</p>
  <div class="more">READ MORE <svg width="13" height="13"><circle cx="6.5" cy="6.5" r="6" fill="#2fbfca"/><path d="M5 4l2.5 2.5L5 9" stroke="#fff" stroke-width="1.6" fill="none"/></svg></div>
</article>
<article class="card" style="left:445px">
  <div class="thumb" role="img" aria-label="Person meditating with a face mask at home" style="background:radial-gradient(ellipse 80px 90px at 110px 130px,#d8b8ac,rgba(216,184,172,0) 90%),linear-gradient(135deg,#5e6e4a 0%,#a9b08a 40%,#e6dccd 75%,#f4efe6 100%)"></div>
  <div class="date"><svg width="12" height="12"><rect x="1" y="2" width="10" height="9" fill="none" stroke="#2fbfca" stroke-width="1.5"/><path d="M1 5h10" stroke="#2fbfca" stroke-width="1.2"/></svg>April 27, 2021</div>
  <h3>Lorem ipsum dolor sit amet</h3>
  <p>Sed ut perspiciatis unde omnis iste natus error sit voluptatem accusantium</p>
  <div class="more">READ MORE <svg width="13" height="13"><circle cx="6.5" cy="6.5" r="6" fill="#2fbfca"/><path d="M5 4l2.5 2.5L5 9" stroke="#fff" stroke-width="1.6" fill="none"/></svg></div>
</article>
<article class="card" style="left:778px">
  <div class="thumb" role="img" aria-label="Hand placing stones on a wooden tray with candles" style="background:radial-gradient(ellipse 130px 30px at 140px 120px,#9a6a3a,rgba(154,106,58,0) 90%),radial-gradient(ellipse 60px 90px at 260px 90px,#3e5a2a,rgba(62,90,42,0) 90%),linear-gradient(180deg,#cfb59a 0%,#e7dccf 55%,#f3ede6 100%)"></div>
  <div class="date"><svg width="12" height="12"><rect x="1" y="2" width="10" height="9" fill="none" stroke="#2fbfca" stroke-width="1.5"/><path d="M1 5h10" stroke="#2fbfca" stroke-width="1.2"/></svg>April 27, 2021</div>
  <h3>Lorem ipsum dolor sit amet</h3>
  <p>Sed ut perspiciatis unde omnis iste natus error sit voluptatem accusantium</p>
  <div class="more">READ MORE <svg width="13" height="13"><circle cx="6.5" cy="6.5" r="6" fill="#2fbfca"/><path d="M5 4l2.5 2.5L5 9" stroke="#fff" stroke-width="1.6" fill="none"/></svg></div>
</article>

<footer class="abs footer">
  <div class="abs brand"><span class="dot"></span>BrightNook</div>
  <div class="abs socials"><span></span><span></span><span></span><span></span></div>
  <div class="abs fcol company"><h4>COMPANY</h4><ul><li>Shop</li><li>Our Story</li><li>Blog</li><li>Stress Symptoms</li><li>Wellness Practices</li></ul></div>
  <div class="abs fcol info"><h4>INFORMATION</h4><ul><li>Terms &amp; Conditions</li><li>Privacy Policy</li><li>Disclaimer</li><li>Site Map</li><li>Club Rewards</li></ul></div>
  <div class="abs fcol news"><h4>SUBSCRIBE OUR NEWSLETTER</h4><p>Subscribe to our mailing list to receives daily updates<br>direct to your inbox!</p></div>
  <div class="abs email">Email Address</div>
  <div class="abs subscribe">SUBSCRIBE</div>
  <div class="abs rule"></div>
  <div class="abs copy">Copyrights © YourBrightNook 2021 | Allrights Reserved</div>
  <div class="abs chat"><svg width="20" height="16"><rect x="1" y="1" width="18" height="12" rx="4" fill="#fff"/><path d="M5 6h10M5 9h7" stroke="#2fbfca" stroke-width="1.6"/></svg></div>
</footer>

</body>
</html>
```